Brintel Works - Fast, Efficient and Gas Mainteance for Domestic, Commercial and Industrial clients

We are in the process of purchasing a new business and would like to get a new logo and business card.
Business is a gas maintenance business that also does new gas installations.
Has been established since 1988.
Services include:
Install all types of gas appliances & equipment inc. hot water units
Maintain / repair / replace all types of gas appliances & equipment

Target Market(s)

Domestic, Commercial and Industrial clients

Industry/Entity Type

Business

Contact Information for Business Card

admin@brintelworks.com.au
07 3918 4726
Brintel Works PTY LTD

Logo Text

Gas Fitting & Plumbing Maintenance Specialists

Font styles to use
Sans Serif

Requirements
Must have
• Logo
• Business name, contact number, email address, web address
• Domestic | Commercial | Industrial Est Since 1988
Nice to have
• Possibly a black card with a flame logo to one side
Should not have
• Spelling errors

```html
<!DOCTYPE html>
<html lang="en">
<head>
<meta charset="utf-8">
<title>Brintel Works – Business Card</title>
<link href="https://fonts.googleapis.com/css2?family=Source+Sans+3:wght@400;600;700&display=swap" rel="stylesheet">
<style>
  :root {
    --backdrop-top: #7d7d7d;
    --backdrop-bottom: #9c9c9c;
    --card-black: #000000;
    --text-white: #ffffff;
    --brand-yellow: #f5d50a;
    --brand-orange: #e8731f;
    --flame-deep: #3a2516;
    --flame-warm: #6b4a33;
  }
  * { margin: 0; padding: 0; box-sizing: border-box; }
  html, body { width: 1200px; height: 900px; overflow: hidden; }
  body {
    position: relative;
    background: linear-gradient(to bottom, var(--backdrop-top), var(--backdrop-bottom));
    font-family: "Source Sans 3", "Myriad Pro", sans-serif;
    color: var(--text-white);
  }
  .card {
    position: absolute;
    top: 306px;
    width: 440px;
    height: 271px;
    border-radius: 10px;
    background: var(--card-black);
    overflow: hidden;
  }
  .card--front { left: 149px; }
  .card--back { left: 608px; }

  .brand-mark {
    position: absolute;
    display: flex;
    align-items: center;
    gap: 8px;
    font-weight: 700;
    white-space: nowrap;
  }
  .brand-mark__dot {
    width: 12px; height: 12px; border-radius: 50%;
    background: var(--brand-orange);
  }
  .card--front .brand-mark {
    left: 38px; top: 140px;
    font-size: 25px;
    color: var(--brand-yellow);
  }
  .card--back .brand-mark {
    left: 0; right: 0; top: 168px;
    justify-content: center;
    font-size: 30px;
    color: var(--text-white);
    z-index: 2;
  }
  .card--back .brand-mark__dot { background: var(--text-white); }

  .address {
    position: absolute; left: 228px; top: 78px;
    font-size: 12.5px; font-weight: 600; line-height: 16px;
  }
  .contact-list {
    position: absolute; left: 228px; top: 137px;
    list-style: none;
    font-size: 12.5px; font-weight: 600; line-height: 16px;
  }
  .contact-list li { display: flex; align-items: center; gap: 9px; }
  .contact-list svg { width: 10px; height: 10px; flex: none; }
  .tagline {
    position: absolute; left: 0; right: 0; top: 222px;
    text-align: center;
    font-size: 12.5px; font-weight: 600;
  }

  .flame-backdrop {
    position: absolute; inset: 0;
    background:
      radial-gradient(ellipse 90px 110px at 70px 230px, var(--flame-deep), transparent 70%),
      radial-gradient(ellipse 80px 130px at 330px 120px, var(--flame-warm), transparent 70%),
      radial-gradient(ellipse 70px 100px at 400px 220px, var(--flame-deep), transparent 70%),
      radial-gradient(ellipse 60px 90px at 280px 230px, var(--flame-deep), transparent 70%);
    opacity: 0.85;
  }
</style>
</head>
<body>
  <section class="card card--front">
    <div class="brand-mark"><span class="brand-mark__dot"></span>Brintel Works</div>
    <p class="address">12345, Address Goes Here<br>Country Name, 123456.</p>
    <ul class="contact-list">
      <li>
        <svg viewBox="0 0 10 10"><path d="M2 1 L4 1 L4.6 3 L3.4 4 Q4.3 5.8 6 6.6 L7 5.4 L9 6 L9 8 Q8.5 9 7.5 9 Q2 8 1 2.5 Q1 1.5 2 1Z" fill="var(--brand-orange)"/></svg>
        07 3918 4726
      </li>
      <li>
        <svg viewBox="0 0 10 10"><rect x="1" y="2.5" width="8" height="5.5" fill="var(--brand-orange)"/><path d="M1 2.5 L5 5.5 L9 2.5" stroke="#000" stroke-width="0.8" fill="none"/></svg>
        admin@brintelworks.com.au
      </li>
      <li>
        <svg viewBox="0 0 10 10"><circle cx="5" cy="5" r="4" fill="var(--brand-orange)"/><path d="M1 5 H9 M5 1 V9" stroke="#000" stroke-width="0.7"/></svg>
        www.brintelworks.com.au
      </li>
    </ul>
    <p class="tagline">Domestic | Commercial | Industrial Est Since 1988</p>
  </section>

  <section class="card card--back">
    <div class="flame-backdrop" role="img" aria-label="Dim photograph of flames in warm brown tones behind the name"></div>
    <div class="brand-mark"><span class="brand-mark__dot"></span>Brintel Works</div>
  </section>
</body>
</html>
```